One of Australia's fastest growing energy maintenance contractors needs a new website

www.brightleaf.com.au
Our business has evolved over the past years and now our website is no longer relevant.
We clean solar panels and we vacuum roof gutters.
We clean solar panels on the roofs of residential houses right up to billion dollar solar farms with in excess of 1 million panels. We offer thermal image testing and bird proofing for our residential and commercial clients and thermal drone imaging services for our solar farm clients.
We vacuum clean roof gutters (using a LoftSuck) on the residential house next door right up to enormous private and public schools, colleges, shopping centres, strat complexes and commercial buildings.
When first built our business had more of a domestic residential skew and the website reflected that. While that is still part of our core business we are now bidding on and have secured large government, commercial and infrastructure contracts and our new website needs to reflect our growth and our new business. We need a new site that it optimised for both desktop ad phone viewing as our latest figures showed that 73% of people visiting our site are on mobile phones. We have an extensive amount of data on Tallymark Insights available as well as Bidlines. Both that would also need integrating with the site along with a few other plugins such as Quilro Chat IQ, Chatterbox etc along with SEO key words etc. We are also the winner and finalists over multiple years of the small business of the year awards and we like to proudly and prominently display those on our site.
We are looking for a new site with a modern professional feel / theme
There is a definitive break in our business between the solar Panel cleaning clients and the gutter cleaning clients so we would like a home page that begins with a simple choice:
Solar Panel Cleaning – Gutter Cleaning
With a professional full screen background image (we have hundreds to choose from) and along the bottom a small area with rights reserved etc, phone number etc (at some point in the future we will split these into two businesses but for now it’s what we have).
After that selection is made we would like a repeat of that same scenario but the selection is:
If it’s Solar Panel Cleaning
(new background image)
Government – Infrastructure – Commercial – Residential
If it’s Gutter Cleaning
(new background image)
Government – Strata – Commercial – Residential
After making those choices then onto the relevant pages with background images relevant to each sector and a them that suits (on the residential we would like to keep the link to our tallymark reviews) - We will provide copy / text for each relevant page.
Other than that, a menu inclusive of the above and:
Resellers Portal – we will provide a link to this from Quilro CRM)
Customer portal (we will supply a link to this from our booking system)
We also need a page for our Solar Resellers / Partners page but we will give them a link to this, it won’t be listed on the site.
Request a quote page (Again we will provide information from Quilro as this will be linked to the CRM)
Standard contact us page inclusive of phone numbers, address and fields supplied from CRM
Sydney – 02 7391 8056
Southern Highlands – 02 4863 1708
Goulburn – 02 4863 1708
Canberra – 02 6172 4385
Wollongong – 02 4239 5817
sales@brightleaf.com.au
Head Office - Kellerton NSW 2590
ABN: 48093716552
Responsive Design: Optimized for desktop and mobile (73% mobile visitors).
Fast Loading Speed: Optimized for performance.
Smooth Transition Animations: For service and category selection.
Sticky Contact Bar: Always accessible at the bottom of mobile screens for quick calls.
SEO Optimization: Focused on government tenders, large-scale commercial contracts, and infrastructure projects.
Integrations
Tallymark Insights & Tallymark Bidlines.
Quilro Chat IQ.
Chatterbox Beacon.
SEO tools and keyword optimization.
Many many more images available if needed
Target Market(s)
Residential, commercial, Government

```html
<!DOCTYPE html>
<html lang="en">
<head>
<meta charset="utf-8">
<title>Gutter Cleaning | Brightleaf</title>
<link href="https://fonts.googleapis.com/css2?family=Figtree:wght@400;500;600;700&display=swap" rel="stylesheet">
<style>
:root{
  --blue:#1d5ea8;
  --blue-dark:#123f75;
  --cyan:#1fb0e6;
  --ink:#111418;
  --muted:#8a8f96;
  --grey-bg:#f4f4f4;
  --line:#d9dbde;
  --star:#f6b400;
  --footer:#0c0d0f;
  --white:#ffffff;
}
*{box-sizing:border-box;margin:0;padding:0}
html,body{width:1200px;height:3297px;overflow:hidden}
body{font-family:"Figtree",sans-serif;color:var(--ink);background:var(--white);position:relative}
.abs{position:absolute}
.btn{position:absolute;display:flex;align-items:center;justify-content:center;gap:8px;border:1.5px solid var(--blue);border-radius:20px;color:var(--blue);font-size:11px;font-weight:600;background:transparent;text-decoration:none}
.btn svg{width:16px;height:8px}
.btn--light{border-color:var(--white);color:var(--white)}

/* header */
.site-header{position:absolute;left:0;top:0;width:1200px;height:62px;background:var(--white);z-index:3}
.logo-tab{position:absolute;left:132px;top:0;width:114px;height:128px;z-index:4}
.logo-tab__name{position:absolute;left:0;width:114px;top:62px;text-align:center;font-size:17px;font-weight:600;color:var(--blue)}
.logo-tab__dot{position:absolute;left:44px;top:18px;width:26px;height:26px;border-radius:50%;background:var(--blue)}
.nav{position:absolute;top:24px;font-size:10px;font-weight:500;color:var(--ink)}

/* hero */
.hero{position:absolute;left:0;top:62px;width:1200px;height:530px;background:linear-gradient(100deg,#5b5a4c 0%,#6f6a58 25%,#3d4656 55%,#2b3340 80%,#1c222c 100%)}
.hero__shade{position:absolute;inset:0;background:rgba(0,0,0,.25)}
.hero__mark{position:absolute;left:580px;top:122px;width:40px;height:40px;border-radius:50%;border:2px solid var(--white)}
.hero__title{position:absolute;left:0;width:1200px;top:180px;text-align:center;color:var(--white);font-size:56px;font-weight:500}
.hero__lead{position:absolute;left:220px;width:760px;top:264px;text-align:center;color:var(--white);font-size:22px;line-height:33px}

/* reviews */
.section-title{position:absolute;left:0;width:1200px;text-align:center;font-size:38px;font-weight:500}
.review-bar{position:absolute;left:207px;top:755px;width:786px;height:42px;background:var(--white);box-shadow:0 1px 4px rgba(0,0,0,.15);display:flex;align-items:center;padding:0 14px;font-size:11px;font-weight:600;gap:8px}
.review-bar__brand{font-size:16px;font-weight:500;color:#4a7fe0}
.stars{color:var(--star);letter-spacing:1px}
.review-bar__cta{margin-left:auto;background:#3c7ee6;color:var(--white);padding:6px 13px;border-radius:2px;font-size:10px}
.review-card{position:absolute;top:810px;width:255px;height:167px;background:var(--white);box-shadow:0 1px 4px rgba(0,0,0,.15);padding:16px 15px}
.review-card__avatar{position:absolute;left:15px;top:16px;width:28px;height:28px;border-radius:50%;background:#7d8a91}
.review-card__name{position:absolute;left:55px;top:16px;font-size:11px;font-weight:600}
.review-card__date{position:absolute;left:55px;top:31px;font-size:9px;color:var(--muted)}
.review-card__src{position:absolute;right:15px;top:16px;width:12px;height:12px;border-radius:50%;background:#4a7fe0}
.review-card__stars{position:absolute;left:15px;top:50px;font-size:14px}
.review-card__text{position:absolute;left:15px;right:15px;top:72px;font-size:10.5px;line-height:16px;display:-webkit-box;-webkit-line-clamp:4;-webkit-box-orient:vertical;overflow:hidden}
.review-card__more{position:absolute;left:15px;top:139px;font-size:9.5px;color:var(--muted)}

/* why */
.why{position:absolute;left:0;top:1123px;width:1200px;height:641px;background:var(--grey-bg)}
.why__frame{position:absolute;left:269px;top:1206px;width:280px;height:236px;border:2px solid var(--blue)}
.why__photo{position:absolute;left:200px;top:1222px;width:331px;height:298px;background:linear-gradient(160deg,#5f9fd8 0%,#8db8dc 35%,#3f6b4a 60%,#2e3034 100%)}
.why__title{position:absolute;left:613px;top:1248px;font-size:38px;font-weight:500}
.why__item{position:absolute;font-size:12.5px;font-weight:500;display:flex;align-items:center;gap:8px}
.why__item svg{width:12px;height:12px}

/* video */
.video{position:absolute;left:106px;top:1591px;width:988px;height:406px;background:linear-gradient(115deg,#6e8b3e 0%,#85a24b 35%,#3c5c93 55%,#4f72ae 100%)}
.video__play{position:absolute;left:469px;top:179px;width:50px;height:50px;border-radius:50%;background:var(--white);display:flex;align-items:center;justify-content:center}

/* accordion */
.accordion{position:absolute;left:261px;top:2157px;width:675px}
.acc-row{position:relative;height:48px;border-top:1.5px solid var(--line);display:flex;align-items:center;padding-left:26px;font-size:21px}
.acc-row__icon{position:absolute;right:26px;top:19px;width:20px;height:8px}
.acc-panel{position:relative;height:272px;background:var(--grey-bg);border-top:1.5px solid var(--line)}
.acc-panel__title{position:absolute;left:26px;top:12px;font-size:21px;font-weight:600;color:var(--blue)}
.acc-panel__text{position:absolute;left:26px;top:86px;width:302px;font-size:8.6px;line-height:15px;color:#333}
.acc-panel__text b{color:var(--blue);font-weight:600}
.acc-panel__photo{position:absolute;left:400px;top:66px;width:251px;height:187px;background:linear-gradient(135deg,#4d4a45 0%,#b6561f 45%,#f08a1c 60%,#3c3b39 100%)}

/* cta band */
.cta{position:absolute;left:0;top:2601px;width:1200px;height:312px;overflow:hidden}
.cta__photo{position:absolute;inset:0;background:linear-gradient(100deg,#2f3a4c 50%,#3e4a5e 70%,#232c38 100%)}
.cta__panel{position:absolute;left:0;top:0;width:1200px;height:312px}
.cta__title{position:absolute;left:106px;top:54px;color:var(--white);font-size:38px;line-height:54px;font-weight:400}

/* footer */
.footer{position:absolute;left:0;top:2913px;width:1200px;height:384px;background:var(--footer);color:var(--white)}
.footer__brand{position:absolute;left:200px;top:98px;font-size:32px;font-weight:500}
.footer__brand-dot{position:absolute;left:258px;top:18px;width:72px;height:72px;border-radius:14px;background:var(--cyan);transform:rotate(45deg) scale(.75)}
.footer__heading{position:absolute;top:79px;font-size:13px;font-weight:500;display:flex;align-items:center;gap:14px}
.footer__heading::after{content:"";display:block;width:100px;height:1px;background:#777}
.footer__list{position:absolute;list-style:none;font-size:10px}
.footer__contact li{height:25px;display:flex;align-items:center;gap:9px}
.footer__contact svg{width:9px;height:9px;flex:none}
.footer__links li{height:25px;display:flex;align-items:center}
.social{position:absolute;left:969px;width:30px;height:30px;border-radius:50%;background:#2a2c30}
.footer__bottom{position:absolute;top:318px;font-size:9.5px}
</style>
</head>
<body>

<header class="site-header">
  <svg class="abs" style="left:132px;top:0" width="114" height="128" viewBox="0 0 114 128" aria-hidden="true">
    <path d="M0 62 H114 L66 122 Q57 132 48 122 Z" fill="#fff"/>
  </svg>
  <span class="nav" style="left:675px">Resellers Portal</span>
  <span class="nav" style="left:775px">Customer portal</span>
  <span class="nav" style="left:878px">Contact us</span>
  <a class="btn" style="left:957px;top:13px;width:137px;height:36px">Request a Quote <svg viewBox="0 0 16 8"><path d="M0 4H15M11 1L15 4L11 7" fill="none" stroke="currentColor"/></svg></a>
</header>
<div class="logo-tab">
  <span class="logo-tab__dot"></span>
  <span class="logo-tab__name">Brightleaf</span>
</div>

<section class="hero" role="img" aria-label="House eaves with dark roof gutters and a downpipe, trees in the background">
  <div class="hero__shade"></div>
  <span class="hero__mark"></span>
  <h1 class="hero__title">Gutter Cleaning</h1>
  <p class="hero__lead">Blocked gutters may appear insignificant, but ensuring their proper functioning brings numerous benefits to your home.</p>
  <a class="btn btn--light" style="left:531px;top:363px;width:137px;height:36px">Request a Quote <svg viewBox="0 0 16 8"><path d="M0 4H15M11 1L15 4L11 7" fill="none" stroke="currentColor"/></svg></a>
</section>

<h2 class="section-title" style="top:670px">We Love Happy Customers</h2>
<div class="review-bar">
  <span class="review-bar__brand">Tallymark</span>
  <span>Excellent</span><span class="stars">★★★★★</span><span>4.9 | 392 reviews</span>
  <span class="review-bar__cta">Write a review</span>
</div>

<article class="review-card" style="left:207px">
  <span class="review-card__avatar"></span><span class="review-card__src"></span>
  <span class="review-card__name">Tessa Marlow</span><span class="review-card__date">16 January 2025</span>
  <span class="review-card__stars stars">★★★★★</span>
  <p class="review-card__text">Brightleaf came on time. I was really well informed of any delay. The report is great and the feedback on our gutters and solar panels is full of detail. The before and after photos were great.</p>
  <span class="review-card__more">Read more</span>
</article>
<article class="review-card" style="left:473px">
  <span class="review-card__avatar" style="background:#1e3f78"></span><span class="review-card__src"></span>
  <span class="review-card__name">Corvinia</span><span class="review-card__date">8 January 2025</span>
  <span class="review-card__stars stars">★★★★★</span>
  <p class="review-card__text">Fantastic service all round.<br>Easy to set up the job and get a quote.<br>The quoted price was reasonable.<br>The person who came to do the work was friendly.</p>
  <span class="review-card__more">Read more</span>
</article>
<article class="review-card" style="left:739px">
  <span class="review-card__avatar" style="background:#b9a9a0"></span><span class="review-card__src"></span>
  <span class="review-card__name">Rob HALLORAN</span><span class="review-card__date">20 December 2024</span>
  <span class="review-card__stars stars">★★★★★</span>
  <p class="review-card__text">Another great job Brightleaf do a great job and we use their services at least once a year and will continue. Their reports and photos are proof of a professional service, highly recommended.</p>
  <span class="review-card__more">Read more</span>
</article>
<a class="btn" style="left:531px;top:1011px;width:137px;height:37px">View all Review <svg viewBox="0 0 16 8"><path d="M0 4H15M11 1L15 4L11 7" fill="none" stroke="currentColor"/></svg></a>

<section class="why"></section>
<div class="why__frame"></div>
<div class="why__photo" role="img" aria-label="Worker in overalls pressure washing a roof gutter under a blue sky"></div>
<h2 class="why__title">Why Choose Us</h2>
<svg width="0" height="0" style="position:absolute"><defs><path id="spark" d="M6 0V12M0 6H12" stroke="#1d5ea8" stroke-width="1.6"/></defs></svg>
<div class="why__item" style="left:613px;top:1322px"><svg viewBox="0 0 12 12"><use href="#spark"/></svg>We don't climb on your roof</div>
<div class="why__item" style="left:613px;top:1353px"><svg viewBox="0 0 12 12"><use href="#spark"/></svg>We don't scratch your gutters</div>
<div class="why__item" style="left:613px;top:1385px"><svg viewBox="0 0 12 12"><use href="#spark"/></svg>We don't trash your gardens</div>
<div class="why__item" style="left:843px;top:1322px"><svg viewBox="0 0 12 12"><use href="#spark"/></svg>No mess no fuss</div>
<div class="why__item" style="left:843px;top:1353px"><svg viewBox="0 0 12 12"><use href="#spark"/></svg>Fixed price quotes</div>
<div class="why__item" style="left:843px;top:1385px"><svg viewBox="0 0 12 12"><use href="#spark"/></svg>No leaf left behind!</div>
<a class="btn" style="left:613px;top:1434px;width:137px;height:37px">Request a Quote <svg viewBox="0 0 16 8"><path d="M0 4H15M11 1L15 4L11 7" fill="none" stroke="currentColor"/></svg></a>

<div class="video" role="img" aria-label="Video still of a gutter vacuum hose reaching into a corrugated roof gutter beside a lawn">
  <span class="video__play"><svg width="22" height="22" viewBox="0 0 22 22"><circle cx="11" cy="11" r="10" fill="#1a4f8f"/><path d="M9 7L15 11L9 15Z" fill="#fff"/></svg></span>
</div>

<h2 class="section-title" style="top:2074px;left:-10px">Explore Gutter Cleaning</h2>
<div class="accordion">
  <div class="acc-row">Gutter Cleaning<svg class="acc-row__icon" viewBox="0 0 20 8"><path d="M1 1L10 6L19 1" fill="none" stroke="#1d5ea8" stroke-width="2.2"/></svg></div>
  <div class="acc-panel">
    <h3 class="acc-panel__title">Bushfire Preparation</h3>
    <svg class="acc-row__icon" viewBox="0 0 20 8"><path d="M1 7L10 2L19 7" fill="none" stroke="#1d5ea8" stroke-width="2.2"/></svg>
    <p class="acc-panel__text">Pine needles, leaves, twigs, and other dry debris lying in a gutter can easily serve as fuel for a fire caused by a few floating embers. these embers not only can drift up to a kilometre from a fire, but they are also more apt to ignite in the semi-enclosed area of a gutter. that's why it is pivotal for homeowners to keep their gutters clean during the hot and dry seasons ... <b>[More]</b></p>
    <a class="btn" style="left:26px;top:198px;width:137px;height:37px">Request a Quote <svg viewBox="0 0 16 8"><path d="M0 4H15M11 1L15 4L11 7" fill="none" stroke="currentColor"/></svg></a>
    <div class="acc-panel__photo" role="img" aria-label="Dry leaves burning inside a roof gutter"></div>
  </div>
  <div class="acc-row" style="border-bottom:1.5px solid var(--line)">Complete Service<svg class="acc-row__icon" viewBox="0 0 20 8"><path d="M1 1L10 6L19 1" fill="none" stroke="#1d5ea8" stroke-width="2.2"/></svg></div>
</div>

<section class="cta">
  <div class="cta__photo" role="img" aria-label="Dark clad house with roof gutter and downpipe, leaves in the gutter"></div>
  <svg class="cta__panel" viewBox="0 0 1200 312" aria-hidden="true"><path d="M0 0H716L627 312H0Z" fill="#1fb0e6"/></svg>
  <h2 class="cta__title">Get the full treatment and<br>have peace of mind this<br>summer season</h2>
  <a class="btn btn--light" style="left:106px;top:228px;width:137px;height:37px">Request a Quote <svg viewBox="0 0 16 8"><path d="M0 4H15M11 1L15 4L11 7" fill="none" stroke="currentColor"/></svg></a>
</section>

<footer class="footer">
  <span class="footer__brand-dot"></span>
  <span class="footer__brand">Brightleaf</span>

  <h4 class="footer__heading" style="left:468px">Contact us</h4>
  <ul class="footer__list footer__contact" style="left:468px;top:103px">
    <li><svg viewBox="0 0 9 9"><circle cx="4.5" cy="3.5" r="3" fill="#1fb0e6"/></svg><span><b>Head Office</b> - Kellerton NSW 2590</span></li>
    <li><svg viewBox="0 0 9 9"><rect x="0.5" y="2" width="8" height="6" fill="#1fb0e6"/></svg>sales@brightleaf.com.au</li>
    <li><svg viewBox="0 0 9 9"><path d="M1 1Q1 8 8 8" stroke="#1fb0e6" stroke-width="2" fill="none"/></svg><span><b>Sydney</b> - 02 7391 8056</span></li>
    <li><svg viewBox="0 0 9 9"><path d="M1 1Q1 8 8 8" stroke="#1fb0e6" stroke-width="2" fill="none"/></svg><span><b>Southern Highlands</b>- 02 4863 1708</span></li>
    <li><svg viewBox="0 0 9 9"><path d="M1 1Q1 8 8 8" stroke="#1fb0e6" stroke-width="2" fill="none"/></svg><span><b>Goulburn</b> - 02 4863 1708</span></li>
    <li><svg viewBox="0 0 9 9"><path d="M1 1Q1 8 8 8" stroke="#1fb0e6" stroke-width="2" fill="none"/></svg><span><b>Canberra</b> - 02 6172 4385</span></li>
    <li><svg viewBox="0 0 9 9"><path d="M1 1Q1 8 8 8" stroke="#1fb0e6" stroke-width="2" fill="none"/></svg><span><b>Wollongong</b> - 02 4239 5817</span></li>
  </ul>

  <h4 class="footer__heading" style="left:731px">Quick links</h4>
  <ul class="footer__list footer__links" style="left:731px;top:107px">
    <li>Home</li><li>Solar Cleaning</li><li>Gutter Cleaning</li><li>DustLift</li><li>Contact us</li><li>Terms and conditions</li><li>Privacy policy</li>
  </ul>

  <span class="social" style="top:86px"></span>
  <span class="social" style="top:123px"></span>
  <span class="social" style="top:161px"></span>
  <span class="social" style="top:199px"></span>

  <p class="footer__bottom" style="left:200px">© 2025 <b>Brightleaf.</b> All Right Reserved</p>
  <p class="footer__bottom" style="left:468px"><b>ABN:</b> 48093716552</p>
  <svg class="abs" style="left:1087px;top:316px" width="14" height="14" viewBox="0 0 14 14" aria-hidden="true"><path d="M7 0L13 14L7 10L1 14Z" fill="#1d7fe0"/></svg>
</footer>

</body>
</html>
```